PLW Gourmet Fungi web presence and site

The goal is to attract local buyers of fresh mushrooms and to both local and international buyers freeze dried mushrooms. Mushrooms grown will be oyster mushrooms (yellow, pink, blue, king), shiitake, lions main, chestnut, and more. My business will also be selling grow kits that help families who would like to grow there own mushrooms

Target Market(s)

Local restaurants, foodies and people seeking high quality fresh and freeze dried gourmet mushrooms

Font styles to use
Serif

Requirements
Must have
• Pictures of the various mushrooms grown along with the characteristics of each of the mushrooms. Recipes and cooking tips for the various mushrooms. There needs to be
1. Order forms with online payments
2. Feedback
3. Preorders for mushrooms that may be more seasonal
4.links to social media Facebook, LinkedIn, etc... I am not knowledgeable in this area
5. Contact Us link email, address, phone
6. About Us link explaining Mark Oduya & Sonia Pettimore and a brief explanation about us and why we became Mushroom farmers
7. Descriptions of the various mushroom varieties grown and how they are best prepared and served
8. Why Freeze Drying mushrooms and the benefits of Freeze Drying over other methods of preservation.
Nice to have
• 1. Recipes and cooking tips for each of the mushrooms.
2. Weekly additional resources added to different pages
3. Q&A section
4. Food Blog with resources added weekly
5.

Flexibility with future expansion and growth is essential. I would like to have a growing site, not a stagnant site.
Should not have
• 1. Boring, bland presentation.
2. The web site is one to educate, promote the various mushrooms grown
3. No music, video or sound on the main pages but eventually a Vlog might be in the works.

I realize there is a lot of content requested but the content needs to attract buyers and to have the site a go to site for foodies

```html
<!DOCTYPE html>
<html lang="en">
<head>
<meta charset="utf-8">
<title>PLW Gourmet Fungi</title>
<link rel="stylesheet" href="https://fonts.googleapis.com/css2?family=Prata&family=Poppins:wght@400;500;600&display=swap">
<style>
:root{
  --orange:#f0621f;
  --orange-deep:#d9501a;
  --peach:#fde8e0;
  --ink:#2a2a2a;
  --body:#555;
  --dark:#35302e;
  --white:#fff;
  --serif:'Prata', Georgia, serif;
  --sans:'Poppins', Arial, sans-serif;
}
html,body{margin:0;padding:0;overflow:hidden;background:var(--white);}
.page{position:relative;width:1200px;height:5314px;overflow:hidden;font-family:var(--sans);color:var(--ink);}
.abs{position:absolute;}
p{margin:0;}
h1,h2,h3{margin:0;font-weight:400;font-family:var(--serif);}

/* hero */
.hero-bg{left:0;top:0;width:1200px;height:880px;}
.brand{display:flex;align-items:center;gap:12px;color:var(--white);font-family:var(--serif);font-size:22px;line-height:26px;}
.brand-dot{width:40px;height:40px;border-radius:50%;background:var(--white);flex:none;}
.social-top{left:764px;top:20px;display:flex;gap:9px;}
.social-top span,.social-foot span{border-radius:50%;box-sizing:border-box;display:flex;align-items:center;justify-content:center;}
.social-top span{width:38px;height:38px;border:2px solid var(--white);}
.order-btn{left:958px;top:18px;width:130px;height:44px;border:2px solid var(--white);border-radius:22px;box-sizing:border-box;color:var(--white);font-size:14px;font-weight:500;display:flex;align-items:center;justify-content:center;}
.nav{left:576px;top:92px;display:flex;gap:29px;color:var(--white);font-size:14px;font-weight:500;}
.nav .active{border-bottom:2px solid var(--white);padding-bottom:4px;}
.hero-title{right:111px;top:256px;text-align:right;color:var(--white);font-size:62px;line-height:70px;text-shadow:0 2px 8px rgba(0,0,0,.35);}
.hero-title span{display:block;font-size:50px;line-height:60px;}
.btn{display:flex;align-items:center;justify-content:center;border-radius:30px;font-size:19px;font-weight:500;color:var(--white);}
.btn-solid{background:var(--orange);border:3px solid var(--white);box-sizing:border-box;}
.btn-line{border:2px solid var(--white);box-sizing:border-box;}

/* sections */
.section-title{left:0;width:1200px;text-align:center;font-size:42px;color:var(--orange);}
.lead{left:118px;width:964px;text-align:center;font-size:13px;line-height:26px;color:var(--body);}
.photo{box-shadow:0 6px 18px rgba(0,0,0,.18);}
.card-img{width:308px;height:233px;}
.card-name{width:308px;text-align:center;font-family:var(--serif);font-size:24px;color:var(--ink);}
.card-text{width:308px;text-align:center;font-size:14px;line-height:24px;color:var(--body);}
.arrow{width:30px;height:58px;}

.about-bg{left:0;top:1423px;width:1200px;height:800px;background:var(--peach);}
.person-img{width:328px;height:254px;}

.freeze-title{color:var(--white);font-size:38px;line-height:52px;}
.freeze-text{width:466px;text-align:justify;color:var(--white);font-size:13px;line-height:26px;}

.grown-title{left:0;width:1200px;text-align:center;font-size:34px;line-height:43px;color:var(--ink);}

.recipe-title{left:584px;top:3576px;font-size:42px;line-height:56px;color:var(--orange);}
.recipe-text{left:584px;top:3698px;width:504px;text-align:justify;font-size:13px;line-height:26px;color:var(--body);}
.icon-circle{width:78px;height:78px;border-radius:50%;box-sizing:border-box;border:4px solid #d8d8d8;display:flex;align-items:center;justify-content:center;}

.feedback-bg{left:0;top:4066px;width:1200px;height:800px;}
.stars{width:308px;display:flex;justify-content:center;gap:6px;}

.footer-brand{left:113px;top:4969px;display:flex;align-items:center;gap:14px;color:var(--orange);font-family:var(--serif);font-size:32px;line-height:40px;}
.footer-brand .brand-dot{width:54px;height:54px;background:var(--orange);}
.social-foot{left:111px;top:5091px;display:flex;gap:10px;}
.social-foot span{width:50px;height:50px;background:var(--orange);}
.form-title{left:532px;top:4930px;font-size:28px;color:var(--orange);}
.field{height:55px;border:2px solid #d6d6d6;border-radius:28px;box-sizing:border-box;padding-left:16px;display:flex;align-items:center;font-size:14px;color:#777;}
.pay-badge{height:16px;border-radius:2px;}
.rule{left:111px;top:5226px;width:978px;height:2px;background:#444;}
.copy{left:0;top:5264px;width:1200px;text-align:center;font-size:15px;font-weight:500;color:var(--ink);}
</style>
</head>
<body>
<div class="page">

  <!-- Hero -->
  <svg class="abs hero-bg" viewBox="0 0 1200 880" role="img" aria-label="Basket of fresh porcini and brown mushrooms on a rustic wooden table">
    <defs>
      <linearGradient id="heroBase" x1="0" y1="0" x2="1" y2="1">
        <stop offset="0" stop-color="#2c221c"/>
        <stop offset="0.5" stop-color="#4a382a"/>
        <stop offset="1" stop-color="#1f1915"/>
      </linearGradient>
      <radialGradient id="heroWarm" cx="0.27" cy="0.48" r="0.42">
        <stop offset="0" stop-color="#d9a46e"/>
        <stop offset="0.35" stop-color="#a26a3e" stop-opacity="0.9"/>
        <stop offset="1" stop-color="#4a382a" stop-opacity="0"/>
      </radialGradient>
      <linearGradient id="heroTable" x1="0" y1="0" x2="0" y2="1">
        <stop offset="0.55" stop-color="#6b5a4e" stop-opacity="0"/>
        <stop offset="1" stop-color="#8a7a6c" stop-opacity="0.6"/>
      </linearGradient>
    </defs>
    <path d="M0 0H1200V680Q600 880 0 680Z" fill="url(#heroBase)"/>
    <path d="M0 0H1200V680Q600 880 0 680Z" fill="url(#heroWarm)"/>
    <path d="M0 0H1200V680Q600 880 0 680Z" fill="url(#heroTable)"/>
  </svg>

  <div class="abs brand" style="left:113px;top:28px;">
    <span class="brand-dot"></span>
    <span>PLW GOURMET<br>FUNGI</span>
  </div>
  <div class="abs social-top" aria-label="Social media links">
    <span><svg width="18" height="18" viewBox="0 0 24 24"><circle cx="12" cy="12" r="9" fill="none" stroke="#fff" stroke-width="2"/><path d="M3 12h18M12 3q5 9 0 18M12 3q-5 9 0 18" fill="none" stroke="#fff" stroke-width="1.6"/></svg></span>
    <span><svg width="18" height="18" viewBox="0 0 24 24"><path d="M4 5h16v11H10l-5 4v-4H4z" fill="none" stroke="#fff" stroke-width="2" stroke-linejoin="round"/></svg></span>
    <span><svg width="18" height="18" viewBox="0 0 24 24"><circle cx="6" cy="12" r="2.5" fill="#fff"/><circle cx="18" cy="5" r="2.5" fill="#fff"/><circle cx="18" cy="19" r="2.5" fill="#fff"/><path d="M6 12L18 5M6 12l12 7" stroke="#fff" stroke-width="1.8"/></svg></span>
    <span><svg width="18" height="18" viewBox="0 0 24 24"><path d="M12 20s-7-4.5-7-10a4 4 0 017-2.5A4 4 0 0119 10c0 5.5-7 10-7 10z" fill="#fff"/></svg></span>
  </div>
  <div class="abs order-btn">Online Order</div>
  <nav class="abs nav">
    <span class="active">HOME</span><span>ABOUT US</span><span>BENEFITS</span><span>VARIETIES</span><span>BLOG</span><span>CONTACT</span>
  </nav>
  <h1 class="abs hero-title">PLW GOURMET<span>FUNGI</span></h1>
  <div class="abs btn btn-solid" style="left:920px;top:421px;width:168px;height:58px;">Read More</div>

  <!-- Varieties -->
  <h2 class="abs section-title" style="top:866px;">MUSHROOMS AND VARIETIES</h2>
  <svg class="abs arrow" style="left:42px;top:1164px;" viewBox="0 0 30 58"><path d="M27 2L3 29L27 56" fill="none" stroke="#333" stroke-width="2.5"/></svg>
  <svg class="abs arrow" style="left:1126px;top:1164px;" viewBox="0 0 30 58"><path d="M3 2L27 29L3 56" fill="none" stroke="#333" stroke-width="2.5"/></svg>

  <div class="abs card-img photo" style="left:111px;top:969px;background:radial-gradient(ellipse at 45% 50%,#b07c4c 0%,#6e4a2e 35%,#2a2a2c 75%);" role="img" aria-label="Dried shiitake mushrooms on a dark slate"></div>
  <div class="abs card-img photo" style="left:443px;top:969px;background:radial-gradient(ellipse at 50% 30%,#c9a27c 0%,#7a5a40 35%,transparent 60%),linear-gradient(180deg,#3a2a20 0%,#8d8a88 60%,#d9d6d2 100%);" role="img" aria-label="Lion's mane mushrooms on a wooden board"></div>
  <div class="abs card-img photo" style="left:773px;top:969px;background:radial-gradient(ellipse at 50% 40%,#e2c3a0 0%,#b08560 30%,#6a4428 60%,#2a1d16 90%),linear-gradient(#5a7a3a,#5a7a3a);" role="img" aria-label="Chestnut mushrooms in a wooden crate"></div>

  <div class="abs card-name" style="left:111px;top:1222px;">SHIITAKE</div>
  <div class="abs card-name" style="left:443px;top:1222px;">LIONS MAIN</div>
  <div class="abs card-name" style="left:773px;top:1222px;">CHESTNUT</div>
  <p class="abs card-text" style="left:111px;top:1262px;">Nemo enim ipsam voluptatem quia vo luptas sit aspernatur aut odit aut fugit, sed quias.</p>
  <p class="abs card-text" style="left:443px;top:1262px;">Nemo enim ipsam voluptatem quia vo luptas sit aspernatur aut odit aut fugit, sed quias.</p>
  <p class="abs card-text" style="left:773px;top:1262px;">Nemo enim ipsam voluptatem quia vo luptas sit aspernatur aut odit aut fugit, sed quias.</p>

  <!-- About -->
  <div class="abs about-bg"></div>
  <h2 class="abs section-title" style="top:1500px;">ABOUT US</h2>
  <p class="abs lead" style="top:1572px;">Sed ut perspiciatis unde omnis iste natus error sit voluptatem accusantium doloremque laudantium, totam rem aperiam, eaque ipsa quae ab illo inventore veritatis et quasi architecto beatae vitae dicta sunt explicabo. Nemo enim ipsam voluptatem quia voluptas sit aspernatur aut odit aut fugit, sed quia consequuntur magni dolores eos qui ratione voluptatem.</p>
  <div class="abs person-img photo" style="left:177px;top:1699px;background:radial-gradient(ellipse at 50% 80%,#9a6a3e 0%,#6e4a30 35%,transparent 60%),linear-gradient(135deg,#5e4a3c,#8a7464 50%,#3e342e);" role="img" aria-label="Portrait of Mark Oduya"></div>
  <div class="abs person-img photo" style="left:691px;top:1699px;background:radial-gradient(ellipse at 55% 85%,#d69a28 0%,#c08a2a 30%,transparent 55%),linear-gradient(90deg,#e8e6e2,#c9c2ba 50%,#ebe8e4);" role="img" aria-label="Portrait of Sonia Pettimore"></div>
  <div class="abs card-name" style="left:127px;top:1982px;width:428px;">MARK ODUYA</div>
  <div class="abs card-name" style="left:641px;top:1982px;width:428px;">SONIA PETTIMORE</div>
  <p class="abs card-text" style="left:127px;top:2020px;width:428px;">Quis autem vel eum iure reprehenderit qui in ea volup tate velit esse quam nihil molestiae consequatur, vel illum qui dolorem eum fugiat.</p>
  <p class="abs card-text" style="left:641px;top:2020px;width:428px;">Quis autem vel eum iure reprehenderit qui in ea volup tate velit esse quam nihil molestiae consequatur, vel illum qui dolorem eum fugiat.</p>

  <!-- Freeze drying -->
  <svg class="abs" style="left:0;top:2150px;" width="1200" height="580" viewBox="0 0 1200 580" role="img" aria-label="Freeze dried mushrooms in bowls">
    <defs>
      <linearGradient id="orangeGrad" x1="0" y1="0" x2="1" y2="1">
        <stop offset="0" stop-color="#f26a26"/><stop offset="1" stop-color="#e0561a"/>
      </linearGradient>
      <radialGradient id="orangeGlow" cx="0.7" cy="0.75" r="0.5">
        <stop offset="0" stop-color="#ff8a4a" stop-opacity="0.55"/><stop offset="1" stop-color="#ff8a4a" stop-opacity="0"/>
      </radialGradient>
      <linearGradient id="darkGrad" x1="0" y1="0" x2="1" y2="1">
        <stop offset="0" stop-color="#2b2726"/><stop offset="0.6" stop-color="#4a3e38"/><stop offset="1" stop-color="#2a2625"/>
      </linearGradient>
      <radialGradient id="darkGlow" cx="0.8" cy="0.55" r="0.4">
        <stop offset="0" stop-color="#8a6a50" stop-opacity="0.5"/><stop offset="1" stop-color="#8a6a50" stop-opacity="0"/>
      </radialGradient>
    </defs>
    <path d="M0 0Q300 -10 600 4V580H0Z" fill="url(#orangeGrad)"/>
    <path d="M0 0Q300 -10 600 4V580H0Z" fill="url(#orangeGlow)"/>
    <path d="M600 4Q900 18 1200 -6V580H600Z" fill="url(#darkGrad)"/>
    <path d="M600 4Q900 18 1200 -6V580H600Z" fill="url(#darkGlow)"/>
  </svg>
  <h2 class="abs freeze-title" style="left:111px;top:2296px;">WHY FREEZE DRYING<br>MUSHROOMS</h2>
  <h2 class="abs freeze-title" style="left:623px;top:2296px;">BENEFITS OF<br>FREEZE DRYING</h2>
  <p class="abs freeze-text" style="left:111px;top:2414px;">Sed ut perspiciatis unde omnis iste natus error sit voluptatem accu santium doloremque laudantium, totam rem aperiam, eaque ipsa quae ab illo inventore veritatis et quasi architecto beatae vitae dicta sunt explicabo. Nemo enim ipsam voluptatem quia voluptas sit aspernatur aut odit aut fugit, sed quia consequuntur magni dolores eos qui ratione voluptatem.</p>
  <p class="abs freeze-text" style="left:623px;top:2414px;">Sed ut perspiciatis unde omnis iste natus error sit voluptatem accu santium doloremque laudantium, totam rem aperiam, eaque ipsa quae ab illo inventore veritatis et quasi architecto beatae vitae dicta sunt explicabo. Nemo enim ipsam voluptatem quia voluptas sit aspernatur aut odit aut fugit, sed quia consequuntur magni dolores eos qui ratione voluptatem.</p>
  <div class="abs btn btn-line" style="left:111px;top:2598px;width:144px;height:50px;font-size:17px;">Read More</div>
  <div class="abs btn btn-line" style="left:623px;top:2598px;width:144px;height:50px;font-size:17px;">Read More</div>

  <!-- Varieties grown -->
  <h2 class="abs grown-title" style="top:2830px;">VARIOUS MUSHROOM VARIETIES GROWN AND HOW<br>THEY ARE BEST PREPARED AND SERVED</h2>
  <p class="abs lead" style="top:2932px;">Sed ut perspiciatis unde omnis iste natus error sit voluptatem accusantium doloremque laudantium, totam rem aperiam, eaque ipsa quae ab illo inventore veritatis et quasi architecto beatae vitae dicta sunt explicabo. Nemo enim ipsam voluptatem quia voluptas sit aspernatur aut odit aut fugit, sed quia consequuntur magni dolores eos qui ratione voluptatem.</p>
  <div class="abs" style="left:0;top:3060px;width:1200px;height:380px;background:radial-gradient(ellipse 14% 40% at 30% 55%,#e6dccc 0%,#c9b89e 60%,transparent 100%),radial-gradient(ellipse 8% 30% at 58% 65%,#d8cebe 0%,#b39a7a 60%,transparent 100%),radial-gradient(ellipse 8% 38% at 88% 58%,#cdbfa8 0%,#8a7458 60%,transparent 100%),linear-gradient(180deg,#fbfaf8 0%,#ece7e0 45%,#a06a40 63%,#6a3f22 80%,#3e2414 100%);" role="img" aria-label="Mushroom grow kits in glass jars on a wooden windowsill"></div>
  <div class="abs btn" style="left:485px;top:3031px;width:232px;height:58px;background:var(--orange);font-size:19px;">Seasonal Perorder</div>

  <!-- Recipes -->
  <svg class="abs" style="left:113px;top:3526px;" width="428" height="455" viewBox="0 0 428 455" role="img" aria-label="Cook stirring sliced mushrooms in a frying pan">
    <defs>
      <linearGradient id="cookGrad" x1="0" y1="0" x2="1" y2="1">
        <stop offset="0" stop-color="#eae6e0"/><stop offset="0.45" stop-color="#c49a78"/><stop offset="1" stop-color="#6a4c34"/>
      </linearGradient>
      <radialGradient id="panGrad" cx="0.5" cy="0.62" r="0.35">
        <stop offset="0" stop-color="#8a5a32"/><stop offset="0.55" stop-color="#2a2420"/><stop offset="1" stop-color="#2a2420" stop-opacity="0"/>
      </radialGradient>
      <clipPath id="blob"><path d="M60 40Q110 -6 210 8Q330 22 395 60Q432 90 420 200Q410 330 360 410Q320 455 220 440Q90 420 30 370Q-4 340 4 250Q12 110 60 40Z"/></clipPath>
    </defs>
    <g clip-path="url(#blob)">
      <rect width="428" height="455" fill="url(#cookGrad)"/>
      <rect width="428" height="455" fill="url(#panGrad)"/>
    </g>
    <path d="M60 40Q110 -6 210 8Q330 22 395 60Q432 90 420 200Q410 330 360 410Q320 455 220 440Q90 420 30 370Q-4 340 4 250Q12 110 60 40Z" fill="none" stroke="#fff" stroke-width="6"/>
  </svg>
  <h2 class="abs recipe-title">RECIPES &amp; COOKING<br>TIPS</h2>
  <p class="abs recipe-text">Sed ut perspiciatis unde omnis iste natus error sit voluptatem accusan tium doloremque laudantium, totam rem aperiam, eaque ipsa quae ab illo in ventore veritatis et quasi architecto beatae vitae dicta sunt expli cabo. Nemo enim ipsam voluptatem quia voluptas sit aspernatur aut odit aut fugit, sed quia magni dolores eos qui ratione vo luptatem.</p>
  <div class="abs icon-circle" style="left:586px;top:3854px;background:var(--orange);">
    <svg width="40" height="40" viewBox="0 0 40 40"><path d="M4 20Q6 5 20 5Q34 5 36 20Z" fill="none" stroke="#fff" stroke-width="2.5"/><path d="M15 20V33Q20 36 25 33V20" fill="none" stroke="#fff" stroke-width="2.5"/><circle cx="14" cy="13" r="2" fill="#fff"/><circle cx="24" cy="11" r="2" fill="#fff"/></svg>
  </div>
  <div class="abs icon-circle" style="left:681px;top:3854px;background:#5a5a5a;">
    <svg width="40" height="40" viewBox="0 0 40 40"><path d="M6 18Q8 6 20 6Q32 6 34 18Q27 21 20 21Q13 21 6 18Z" fill="none" stroke="#fff" stroke-width="2.5"/><path d="M17 21Q16 28 15 34H25Q24 28 23 21" fill="none" stroke="#fff" stroke-width="2.5"/></svg>
  </div>
  <div class="abs icon-circle" style="left:776px;top:3854px;background:#5a5a5a;">
    <svg width="40" height="40" viewBox="0 0 40 40"><path d="M5 16Q10 6 20 6Q30 6 35 16Z" fill="none" stroke="#fff" stroke-width="2.5"/><path d="M17 16V34H23V16" fill="none" stroke="#fff" stroke-width="2.5"/></svg>
  </div>

  <!-- Feedback -->
  <svg class="abs feedback-bg" viewBox="0 0 1200 800" role="img" aria-label="Forest floor with mushrooms growing in moss">
    <defs>
      <linearGradient id="forestGrad" x1="0" y1="0" x2="0" y2="1">
        <stop offset="0" stop-color="#30312c"/><stop offset="0.55" stop-color="#3a3f2c"/><stop offset="1" stop-color="#5a6e2a"/>
      </linearGradient>
      <radialGradient id="forestGlow" cx="0.85" cy="0.2" r="0.45">
        <stop offset="0" stop-color="#6e6a58" stop-opacity="0.6"/><stop offset="1" stop-color="#6e6a58" stop-opacity="0"/>
      </radialGradient>
    </defs>
    <path d="M0 0H1200V790Q600 686 0 790Z" fill="url(#forestGrad)"/>
    <path d="M0 0H1200V790Q600 686 0 790Z" fill="url(#forestGlow)"/>
  </svg>
  <h2 class="abs section-title" style="top:4146px;color:var(--white);">FEEDBACK</h2>
  <p class="abs lead" style="top:4216px;color:#e8e8e8;">Sed ut perspiciatis unde omnis iste natus error sit voluptatem accusantium doloremque laudantium, totam rem aperiam, eaque ipsa quae ab illo inventore veritatis et quasi architecto beatae vitae dicta sunt explicabo.</p>
  <div class="abs card-img photo" style="left:111px;top:4330px;background:radial-gradient(ellipse at 50% 40%,#d8a47a 0%,#a86a3c 30%,transparent 55%),linear-gradient(180deg,#eeeeea 0%,#dcdcd6 60%,#8a9a68 100%);" role="img" aria-label="Portrait of customer Clara"></div>
  <div class="abs card-img photo" style="left:443px;top:4330px;background:radial-gradient(ellipse at 50% 40%,#b07a58 0%,#4a3026 35%,transparent 58%),linear-gradient(180deg,#f2f2f2 0%,#e4e4e4 60%,#26283a 100%);" role="img" aria-label="Portrait of customer Andrea"></div>
  <div class="abs card-img photo" style="left:773px;top:4330px;background:radial-gradient(ellipse at 45% 50%,#6a4434 0%,#2e221e 35%,transparent 58%),linear-gradient(180deg,#c8d2dc 0%,#e0e4e8 60%,#f0f0f0 100%);" role="img" aria-label="Portrait of customer Smith"></div>
  <div class="abs card-name" style="left:111px;top:4582px;color:var(--white);">CLARA</div>
  <div class="abs card-name" style="left:443px;top:4582px;color:var(--white);">ANDREA</div>
  <div class="abs card-name" style="left:773px;top:4582px;color:var(--white);">SMITH</div>
  <p class="abs card-text" style="left:111px;top:4624px;color:#eee;">Nemo enim ipsam voluptatem quia vo luptas sit aspernatur aut odit aut fugit, sed quias.</p>
  <p class="abs card-text" style="left:443px;top:4624px;color:#eee;">Nemo enim ipsam voluptatem quia vo luptas sit aspernatur aut odit aut fugit, sed quias.</p>
  <p class="abs card-text" style="left:773px;top:4624px;color:#eee;">Nemo enim ipsam voluptatem quia vo luptas sit aspernatur aut odit aut fugit, sed quias.</p>
  <div class="abs stars" style="left:111px;top:4710px;" aria-label="4 out of 5 stars">
    <svg width="26" height="24" viewBox="0 0 24 23"><path d="M12 1l3.2 7 7.6.7-5.7 5 1.7 7.5L12 17.3 5.2 21.2l1.7-7.5-5.7-5 7.6-.7z" fill="#fff"/></svg>
    <svg width="26" height="24" viewBox="0 0 24 23"><path d="M12 1l3.2 7 7.6.7-5.7 5 1.7 7.5L12 17.3 5.2 21.2l1.7-7.5-5.7-5 7.6-.7z" fill="#fff"/></svg>
    <svg width="26" height="24" viewBox="0 0 24 23"><path d="M12 1l3.2 7 7.6.7-5.7 5 1.7 7.5L12 17.3 5.2 21.2l1.7-7.5-5.7-5 7.6-.7z" fill="#fff"/></svg>
    <svg width="26" height="24" viewBox="0 0 24 23"><path d="M12 1l3.2 7 7.6.7-5.7 5 1.7 7.5L12 17.3 5.2 21.2l1.7-7.5-5.7-5 7.6-.7z" fill="#fff"/></svg>
    <svg width="26" height="24" viewBox="0 0 24 23"><path d="M12 1l3.2 7 7.6.7-5.7 5 1.7 7.5L12 17.3 5.2 21.2l1.7-7.5-5.7-5 7.6-.7z" fill="none" stroke="#fff" stroke-width="1.5"/></svg>
  </div>
  <div class="abs stars" style="left:443px;top:4710px;" aria-label="4 out of 5 stars">
    <svg width="26" height="24" viewBox="0 0 24 23"><path d="M12 1l3.2 7 7.6.7-5.7 5 1.7 7.5L12 17.3 5.2 21.2l1.7-7.5-5.7-5 7.6-.7z" fill="#fff"/></svg>
    <svg width="26" height="24" viewBox="0 0 24 23"><path d="M12 1l3.2 7 7.6.7-5.7 5 1.7 7.5L12 17.3 5.2 21.2l1.7-7.5-5.7-5 7.6-.7z" fill="#fff"/></svg>
    <svg width="26" height="24" viewBox="0 0 24 23"><path d="M12 1l3.2 7 7.6.7-5.7 5 1.7 7.5L12 17.3 5.2 21.2l1.7-7.5-5.7-5 7.6-.7z" fill="#fff"/></svg>
    <svg width="26" height="24" viewBox="0 0 24 23"><path d="M12 1l3.2 7 7.6.7-5.7 5 1.7 7.5L12 17.3 5.2 21.2l1.7-7.5-5.7-5 7.6-.7z" fill="#fff"/></svg>
    <svg width="26" height="24" viewBox="0 0 24 23"><path d="M12 1l3.2 7 7.6.7-5.7 5 1.7 7.5L12 17.3 5.2 21.2l1.7-7.5-5.7-5 7.6-.7z" fill="none" stroke="#fff" stroke-width="1.5"/></svg>
  </div>
  <div class="abs stars" style="left:773px;top:4710px;" aria-label="4 out of 5 stars">
    <svg width="26" height="24" viewBox="0 0 24 23"><path d="M12 1l3.2 7 7.6.7-5.7 5 1.7 7.5L12 17.3 5.2 21.2l1.7-7.5-5.7-5 7.6-.7z" fill="#fff"/></svg>
    <svg width="26" height="24" viewBox="0 0 24 23"><path d="M12 1l3.2 7 7.6.7-5.7 5 1.7 7.5L12 17.3 5.2 21.2l1.7-7.5-5.7-5 7.6-.7z" fill="#fff"/></svg>
    <svg width="26" height="24" viewBox="0 0 24 23"><path d="M12 1l3.2 7 7.6.7-5.7 5 1.7 7.5L12 17.3 5.2 21.2l1.7-7.5-5.7-5 7.6-.7z" fill="#fff"/></svg>
    <svg width="26" height="24" viewBox="0 0 24 23"><path d="M12 1l3.2 7 7.6.7-5.7 5 1.7 7.5L12 17.3 5.2 21.2l1.7-7.5-5.7-5 7.6-.7z" fill="#fff"/></svg>
    <svg width="26" height="24" viewBox="0 0 24 23"><path d="M12 1l3.2 7 7.6.7-5.7 5 1.7 7.5L12 17.3 5.2 21.2l1.7-7.5-5.7-5 7.6-.7z" fill="none" stroke="#fff" stroke-width="1.5"/></svg>
  </div>

  <!-- Footer -->
  <div class="abs footer-brand">
    <span class="brand-dot"></span>
    <span>PLW GOURMET<br>FUNGI</span>
  </div>
  <div class="abs social-foot" aria-label="Social media links">
    <span><svg width="22" height="22" viewBox="0 0 24 24"><circle cx="12" cy="12" r="9" fill="none" stroke="#fff" stroke-width="2"/><path d="M3 12h18M12 3q5 9 0 18M12 3q-5 9 0 18" fill="none" stroke="#fff" stroke-width="1.6"/></svg></span>
    <span><svg width="22" height="22" viewBox="0 0 24 24"><path d="M4 5h16v11H10l-5 4v-4H4z" fill="none" stroke="#fff" stroke-width="2" stroke-linejoin="round"/></svg></span>
    <span><svg width="22" height="22" viewBox="0 0 24 24"><circle cx="6" cy="12" r="2.5" fill="#fff"/><circle cx="18" cy="5" r="2.5" fill="#fff"/><circle cx="18" cy="19" r="2.5" fill="#fff"/><path d="M6 12L18 5M6 12l12 7" stroke="#fff" stroke-width="1.8"/></svg></span>
    <span><svg width="22" height="22" viewBox="0 0 24 24"><path d="M12 20s-7-4.5-7-10a4 4 0 017-2.5A4 4 0 0119 10c0 5.5-7 10-7 10z" fill="#fff"/></svg></span>
  </div>

  <h3 class="abs form-title">ONLINE PAYMENT FORM</h3>
  <div class="abs field" style="left:528px;top:4980px;width:274px;">Name</div>
  <div class="abs field" style="left:817px;top:4980px;width:270px;">Phone</div>
  <div class="abs field" style="left:528px;top:5050px;width:274px;">Email</div>
  <div class="abs field" style="left:817px;top:5050px;width:270px;">Message</div>
  <div class="abs btn" style="left:528px;top:5122px;width:136px;height:53px;background:var(--orange);font-size:18px;">Pay Online</div>
  <div class="abs" style="left:686px;top:5134px;display:flex;gap:5px;" aria-label="Accepted payment methods">
    <span class="pay-badge" style="width:26px;background:#e6e6e6;"></span>
    <span class="pay-badge" style="width:26px;background:#d74a3a;"></span>
    <span class="pay-badge" style="width:26px;background:#2f6db5;"></span>
    <span class="pay-badge" style="width:26px;background:#1c3f80;"></span>
    <span class="pay-badge" style="width:26px;background:#4aa3d8;"></span>
    <span class="pay-badge" style="width:26px;background:#f0a640;"></span>
  </div>

  <div class="abs rule"></div>
  <p class="abs copy">Copyrights @ 2020 PLW Gourmet Fungi. All Rights Reserved.</p>
</div>
</body>
</html>
```